Exclusive beauty salon needs a price list or services booklet

I need a new very attractive flyer for my beauty salon, containing information on the different services and their prices.
In attachment you can find a pdf of the "old" one, but I'd love to have a beautifully designed new one!
I'd love to have a booklet in format 148 x 148 mm, or in US format, containing 12 or 16 pages, but if you can offer other nice looking designs they are welcome!
The services that need to come in the booklet with their prices can all be found on my website: www.atelierverano.be, starting with
Gelaatsverzorging
Wimperverlenging
Suikerontharing
Wimperlifting
Permanente Make Up
Airbrush Tanning

Target Market(s)

woman from 20 to 89 years old

Industry/Entity Type

Beauty Salon

Font styles to use
Sans Serif

Colors

Designer to choose colors to be used in the design.

Requirements
Must have
• a classy nice look, it must contain details about the services from my beauty salon and their prices, and nice pictures.
• The Names, prices and explanations of the services can easily be found on my website: www.atelierverano.be
Nice to have
• In attachment you can find the "old" price list in pdf, what I need now is a "new booklet" with the new logo and updated services price list.
• I need a very nice and attractive looking booklet, classy chique, Paris chique, looking very expensive.
Should not have
• Not too much colors, not too curly, but still feminine

```html
<!DOCTYPE html>
<html lang="nl">
<head>
<meta charset="utf-8">
<title>Atelier Verano – Wimperverlenging</title>
<link href="https://fonts.googleapis.com/css2?family=Questrial&display=swap" rel="stylesheet">
<style>
  :root {
    --page-left: #f4f4f4;
    --page-right: #ffffff;
    --rose: #d9a4ad;
    --rose-title: #d38c99;
    --band: #dcaab2;
    --text: #8a8a8a;
    --photo-skin: #e9d6cf;
    --photo-light: #f6eeeb;
    --ink: #555555;
  }
  * { margin: 0; padding: 0; box-sizing: border-box; }
  html, body { width: 1200px; height: 523px; overflow: hidden; background: #ffffff; }
  body { font-family: "Questrial", sans-serif; }
  .spread { position: relative; width: 1200px; height: 523px; display: flex; }
  .page { position: relative; width: 600px; height: 523px; }
  .page--left { background: var(--page-left); padding: 18px 40px 0 54px; color: var(--text); }
  .page--right { background: var(--page-right); }

  .service-title {
    color: var(--rose-title); font-size: 21px; font-weight: 400; line-height: 24px;
    text-transform: uppercase; letter-spacing: 0.2px; margin-bottom: 8px;
  }
  .service-copy p { font-size: 10px; line-height: 11px; margin-bottom: 14px; max-width: 410px; }
  .benefits { list-style: none; position: absolute; left: 54px; top: 278px; width: 335px; }
  .benefits li { font-size: 10px; line-height: 12px; margin-bottom: 12.5px; padding-left: 9px; position: relative; }
  .benefits li::before { content: "•"; position: absolute; left: 0; color: var(--rose); }

  .result-photo { position: absolute; left: 395px; width: 205px; background: linear-gradient(180deg, var(--photo-light), var(--photo-skin)); }
  .result-photo--before { top: 283px; height: 67px; }
  .result-photo--after { top: 354px; height: 72px; }

  .hero-photo {
    position: absolute; left: 0; top: 0; width: 600px; height: 330px;
    background: linear-gradient(180deg, #efe1dc 0%, #f3e9e6 55%, #ffffff 100%);
  }
  .price-band {
    position: absolute; left: 60px; right: 0; height: 21px; background: var(--band);
    color: #ffffff; display: flex; justify-content: space-between; align-items: center;
    padding: 0 55px 0 18px; font-size: 13px; text-transform: uppercase;
  }
  .price-band--first { top: 355px; }
  .price-band--refill { top: 402px; }
  .price-band .price { font-size: 11px; }

  .brand { position: absolute; right: 36px; bottom: 34px; display: flex; align-items: center; gap: 6px; color: var(--ink); font-size: 10px; letter-spacing: 2px; text-transform: uppercase; }
  .brand-mark { width: 7px; height: 7px; background: var(--ink); }
</style>
</head>
<body>
<main class="spread">
  <section class="page page--left">
    <h1 class="service-title">Individuele wimperverlenging Cil Lumière</h1>
    <div class="service-copy">
      <p>Lange, volle en gekrulde wimpers dankzij Cil Lumière.</p>
      <p>Zijden wimpers worden één per één op uw eigen wimpers gekleefd.</p>
      <p>Mascara kan maar is overbodig.</p>
      <p>Cil Lumière wimpers zijn ultralicht en zoveel natuurlijker dan kunststoffen wimperstrips, stukjes en plukjes. Door de exclusief ontwikkelde lijm blijven ze wekenlang in positie. De sneldrogende lijm laat een plaatsing toe van ongeveer 60 wimpers per oog. Een vol effect, in een behandeling van slechts 1/2 uur.</p>
      <p>Na max. 4 weken laten bijwerken garandeert een optimaal en schitterend eindresultaat.</p>
      <p>De zijden wimpers zijn beschikbaar in verschillende lengtes, dikte en krulling of curves.</p>
      <p>Voordelen van Cil Lumière Wimperverlenging op een rijtje</p>
    </div>
    <ul class="benefits">
      <li>Pijnloze behandeling</li>
      <li>Geen beschadiging van de natuurlijke wimpers</li>
      <li>Onmiddellijk een verbluffend resultaat</li>
      <li>Geen nazorg</li>
      <li>Verkrijgbaar in verschillende lengtes, diktes en curves</li>
      <li>Prima oplossing voor feestjes, vakanties, enz.</li>
      <li>Mascara wordt overbodig</li>
      <li>Wimperextensions blijven aangehecht tijdens het zwemmen, douchen en saunabezoek</li>
      <li>Cil Lumière garandeert wekenlang plezier</li>
    </ul>
    <div class="result-photo result-photo--before" role="img" aria-label="Foto van gesloten ogen vóór de wimperverlenging"></div>
    <div class="result-photo result-photo--after" role="img" aria-label="Foto van gesloten ogen na de wimperverlenging"></div>
  </section>

  <section class="page page--right">
    <div class="hero-photo" role="img" aria-label="Foto van een schoonheidsspecialiste die met pincetten wimperextensions plaatst"></div>
    <div class="price-band price-band--first"><span>Eerste plaatsing wimperextensions</span><span class="price">€65</span></div>
    <div class="price-band price-band--refill"><span>Bijwerking na max. 4 weken</span><span class="price">€35</span></div>
    <div class="brand"><span class="brand-mark"></span><span>Atelier Verano</span></div>
  </section>
</main>
</body>
</html>
```